Wireless retailer specializing in sale / purchase of used and refurbished devices. We are an authorized dealer for " vKarma Cellular". Logos for vKarma and our logo have been included.
Business card needs to feature both locations address. We will do a reprint once we have the phone number for the second location and remove the "coming soon" text.
Cards will also need to be personalized per employee. Will post that information as well.
Any suggestions are welcome
Business
The Dial Crew
Birchwood Meadow Plaza Shopping Center
4817 Tamber Lane
Virginia Beach, VA 23464
757.318.6624
Coming in 2014
The Dial Crew 2
Marlow Quarry Shopping Center
2946 Fenwick Rd Suite #208
Virginia Beach, VA 23452

```html
<!DOCTYPE html>
<html lang="en">
<head>
<meta charset="utf-8">
<title>The Dial Crew – Business Card</title>
<link rel="stylesheet" href="https://fonts.googleapis.com/css2?family=Michroma&family=Questrial&display=swap">
<style>
  :root {
    --backdrop: #ebebeb;
    --card-black: #1f1f20;
    --card-black-deep: #141415;
    --pattern-tone: #2a2a2b;
    --brand-blue: #1d5fb0;
    --text-white: #f2f2f2;
    --divider: #8a8a8a;
    --badge-white: #f7f7f7;
  }
  * { margin: 0; padding: 0; box-sizing: border-box; }
  html, body {
    width: 1200px; height: 900px; overflow: hidden;
    background: var(--backdrop);
  }
  .canvas {
    position: relative; width: 1200px; height: 900px;
    display: flex; flex-direction: column; align-items: center; justify-content: center;
    gap: 56px;
  }
  .card {
    position: relative; width: 620px; height: 354px; overflow: hidden;
    box-shadow: 0 4px 14px rgba(0,0,0,0.18);
  }
  /* Front side */
  .card--front {
    background: linear-gradient(160deg, var(--card-black) 0%, var(--card-black-deep) 100%);
  }
  .logo-pattern {
    position: absolute; inset: 0;
    background: linear-gradient(150deg, var(--pattern-tone) 0%, var(--card-black) 55%, var(--pattern-tone) 100%);
    opacity: 0.9;
  }
  .front-wordmark {
    position: absolute; right: 54px; top: 50%; transform: translateY(-50%);
    display: flex; align-items: center; gap: 14px;
    font-family: "Michroma", sans-serif; font-size: 34px; color: var(--text-white);
    letter-spacing: 1px; text-transform: uppercase;
  }
  .wordmark-square {
    width: 22px; height: 22px; background: var(--brand-blue);
  }
  /* Back side */
  .card--back {
    background: var(--card-black);
    padding: 54px 48px 0 50px;
  }
  .back-wordmark {
    font-family: "Michroma", sans-serif; font-size: 30px; color: var(--brand-blue);
    text-transform: uppercase; letter-spacing: 1px;
  }
  .dealer-badge {
    position: absolute; top: 26px; right: 40px;
    width: 118px; height: 38px; border-radius: 4px;
    background: var(--badge-white);
  }
  .locations {
    position: absolute; left: 50px; right: 40px; bottom: 52px;
    display: flex; align-items: flex-end;
  }
  .location { flex: 1; }
  .location + .location {
    border-left: 1px solid var(--divider);
    padding-left: 28px; margin-left: 12px;
  }
  .location__name {
    font-family: "Michroma", sans-serif; font-size: 11.5px; color: var(--brand-blue);
    text-transform: uppercase; margin-bottom: 8px; letter-spacing: 0.3px;
  }
  .location__address {
    font-family: "Questrial", sans-serif; font-style: normal;
    font-size: 14px; line-height: 1.65; color: var(--text-white);
  }
  .location__phone {
    font-family: "Questrial", sans-serif; font-size: 22px; color: var(--brand-blue);
    letter-spacing: 1.5px; margin-top: 12px;
  }
</style>
</head>
<body>
<main class="canvas">
  <section class="card card--front">
    <div class="logo-pattern" role="img" aria-label="Faint repeated brand wordmark pattern across the card"></div>
    <div class="front-wordmark"><span class="wordmark-square"></span>The Dial Crew</div>
  </section>

  <section class="card card--back">
    <div class="back-wordmark">The Dial Crew</div>
    <div class="dealer-badge" role="img" aria-label="vKarma Cellular authorized retailer badge"></div>
    <div class="locations">
      <div class="location">
        <div class="location__name">The Dial Crew</div>
        <address class="location__address">Birchwood Meadow Plaza Shopping Center<br>4817 Tamber Lane<br>Virginia Beach, VA 23464</address>
        <div class="location__phone">757.318.6624</div>
      </div>
      <div class="location">
        <div class="location__name">The Dial Crew #2</div>
        <address class="location__address">Marlow Quarry Shopping Center<br>2946 Fenwick Rd Suite #208<br>Virginia Beach, VA 23452</address>
        <div class="location__phone">757.604.7719</div>
      </div>
    </div>
  </section>
</main>
</body>
</html>
```